Stationery Design Project

I need a stationary design for our company. we are based in Houston, TX and we are called Mira Vell Lending. And we are wanting to brand our MoneyMendPlus program, which includes our tax preparation and restoration, credit repair service. Although our business offers other programs, we are interested in mainly focusing on The MoneyMendPlus program. We are looking for way to brand our ourselves and I believe that a great stationery design will help in achieving this goal. Our logo design is blue and light blue. the slogan is orange.

Industry/Entity Type

Business

Requirements
Must have
• Address: 30871 Calloway Ln. B-22
Houston, TX 75419
Tel. 555-318-6207
Fax 555-294-7153
www.miravelllending.example
info@miravelllending.example
Our Slogan: Happiness, Restored!

```html
<!DOCTYPE html>
<html lang="en">
<head>
<meta charset="utf-8">
<title>MoneyMendPlus Business Cards</title>
<link href="https://fonts.googleapis.com/css2?family=Tinos:wght@400;700&display=swap" rel="stylesheet">
<style>
  :root {
    --page: #eceff2;
    --white: #ffffff;
    --navy: #123f6d;
    --navy-deep: #0b3560;
    --blue: #1565a6;
    --sky: #1a8fd0;
    --orange: #f39322;
    --faint: rgba(255, 255, 255, 0.22);
  }
  * { box-sizing: border-box; margin: 0; padding: 0; }
  html, body {
    width: 1200px; height: 714px; overflow: hidden;
    background: var(--page);
    font-family: "Tinos", "Times New Roman", serif;
  }
  .stage { position: relative; width: 1200px; height: 714px; }
  .card {
    position: absolute; top: 197px; width: 560px; height: 320px;
    overflow: hidden; box-shadow: 0 4px 14px rgba(0,0,0,0.18);
  }

  /* Front */
  .card-front { left: 20px; background: var(--white); }
  .front-brand {
    position: absolute; left: 44px; top: 88px;
    font-size: 50px; color: var(--blue); letter-spacing: -0.5px;
  }
  .front-brand .brand-mark {
    display: inline-block; width: 16px; height: 16px; margin-right: 12px;
    background: var(--orange); vertical-align: middle;
  }
  .partner-badge {
    position: absolute; right: 30px; top: 20px; width: 110px; height: 110px;
    border: 3px solid #c8d4e2; background: var(--navy);
    display: flex; align-items: center; justify-content: center; text-align: center;
    color: var(--white); font-size: 13px; line-height: 1.3; padding: 10px;
  }
  .info-band {
    position: absolute; left: 0; right: 0; bottom: 0; height: 168px;
    background: linear-gradient(200deg, var(--sky) 0%, var(--blue) 45%, var(--navy-deep) 100%);
    color: var(--white);
  }
  .address { position: absolute; left: 26px; top: 18px; font-size: 15px; }
  .contact-list { position: absolute; left: 26px; top: 58px; list-style: none; font-size: 14.5px; }
  .contact-list li { display: flex; align-items: center; height: 22px; }
  .contact-list svg { width: 13px; height: 13px; margin-right: 9px; fill: var(--white); }
  .slogan {
    position: absolute; right: 30px; top: 16px; text-align: center;
    color: var(--orange); font-weight: 700; font-size: 28px; line-height: 1.05;
  }

  /* Back */
  .card-back {
    left: 620px;
    background: radial-gradient(ellipse at 50% 45%, #1f7fbf 0%, #135a93 45%, var(--navy-deep) 100%);
    color: var(--white);
  }
  .back-frame {
    position: absolute; left: 140px; top: 22px; width: 280px; height: 276px;
    border: 4px solid var(--faint); background: rgba(255,255,255,0.05);
  }
  .back-rule {
    position: absolute; left: 82px; top: 132px; width: 400px; height: 4px; background: var(--white);
  }
  .back-brand {
    position: absolute; left: 0; right: 0; top: 138px; text-align: center;
    font-size: 58px; letter-spacing: -0.5px;
  }
  .back-partner {
    position: absolute; left: 0; right: 0; top: 214px; text-align: center;
    font-size: 22px; color: var(--faint); font-weight: 700;
  }
  .back-web {
    position: absolute; left: 0; right: 0; top: 252px; text-align: center;
    font-size: 13px; letter-spacing: 3.5px;
  }
</style>
</head>
<body>
<main class="stage">

  <section class="card card-front" aria-label="Business card front">
    <div class="front-brand"><span class="brand-mark"></span>MoneyMendPlus</div>
    <div class="partner-badge">Mira Vell Lending</div>

    <div class="info-band">
      <p class="address">30871 Calloway Ln. B-22, Houston, TX 75419</p>
      <ul class="contact-list">
        <li>
          <svg viewBox="0 0 16 16" aria-hidden="true"><path d="M3.5 1.5l2.5 0 1 3.5-1.7 1.2a9 9 0 0 0 4.5 4.5L11 9l3.5 1v2.5c0 1-1 2-2 2C6.5 14.5 1.5 9.5 1.5 3.5c0-1 1-2 2-2z"/></svg>
          555-318-6207
        </li>
        <li>
          <svg viewBox="0 0 16 16" aria-hidden="true"><path d="M4 1h7v4H4z M1 6h14v7H1z M4 11h8v4H4z"/></svg>
          555-294-7153
        </li>
        <li>
          <svg viewBox="0 0 16 16" aria-hidden="true"><path d="M1 3h14v10H1z M1 3l7 6 7-6" fill="none" stroke="#fff" stroke-width="1.6"/></svg>
          info@miravelllending.example
        </li>
        <li>
          <svg viewBox="0 0 16 16" aria-hidden="true"><circle cx="8" cy="8" r="6.5" fill="none" stroke="#fff" stroke-width="1.4"/><path d="M1.5 8h13M8 1.5c-3 3.5-3 9.5 0 13M8 1.5c3 3.5 3 9.5 0 13" fill="none" stroke="#fff" stroke-width="1.2"/></svg>
          www.miravelllending.example
        </li>
      </ul>
      <p class="slogan">HAPPINESS<br>RESTORED!</p>
    </div>
  </section>

  <section class="card card-back" aria-label="Business card back">
    <div class="back-frame"></div>
    <div class="back-rule"></div>
    <div class="back-brand">MoneyMendPlus</div>
    <div class="back-partner">Mira Vell Lending</div>
    <div class="back-web">www.miravelllending.example</div>
  </section>

</main>
</body>
</html>
```